Mortgage Company needs some fresh looking business cards to replace current outdated design

Looking for fresh ideas. The only requirement is that the card must show the following:Keelbrook Logo (uploaded)Keelbrook slogan "your logical choice"Equal Housing Lender logo (uploaded)Keelbrook NMLS #572081 (see current bus card, uploaded)Website as shown on sampleColor Codes as follows:Green = PMS 555 , #2b7051 , CMYK 83 33 77 21Rust = PMS 471 , #bc6225 , CMYK 21 70 100 8Would like two sided card. Front will have all of the above info, and back will have just the logo.

Target Market(s)

Consumers and Real Estate Agents

Industry/Entity Type

Mortgage Lender

Contact Information for Business Card

Color Codes as follows:
Green = PMS 555 , #2b7051 , CMYK 83 33 77 21
Rust = PMS 471 , #bc6225 , CMYK 21 70 100 8

Would like two sided card. Front will have all of the above info, and back will have just the logo.

Requirements
Must have
• Keelbrook Logo (uploaded)
• Keelbrook slogan "your logical choice"
• Equal Housing Lender logo (uploaded)
• Keelbrook NMLS #572081 (see current bus card, uploaded)
• Website as shown on sample

```html
<!DOCTYPE html>
<html lang="en">
<head>
<meta charset="utf-8">
<title>Keelbrook Mortgage Business Card</title>
<link href="https://fonts.googleapis.com/css2?family=Playfair+Display:ital,wght@0,400;1,400&family=Open+Sans:wght@400;600&display=swap" rel="stylesheet">
<style>
  :root {
    --green: #2b7051;
    --green-deep: #1f7a62;
    --rust: #bc6225;
    --ink: #111213;
    --paper: #ffffff;
    --stage: #2a2d31;
  }
  * { box-sizing: border-box; margin: 0; padding: 0; }
  html, body { width: 1200px; height: 900px; overflow: hidden; background: var(--stage); }
  .canvas { position: relative; width: 1200px; height: 900px; }

  .card {
    position: absolute; left: 250px; width: 700px; height: 400px;
    overflow: hidden; box-shadow: 0 12px 30px rgba(0,0,0,.45);
  }
  .card-back { top: 40px; background: var(--ink); }
  .card-front { top: 470px; background: var(--paper); }

  .wordmark {
    font-family: "Open Sans", sans-serif; font-weight: 600; color: var(--green-deep);
    white-space: nowrap; line-height: 1;
  }
  .slogan {
    font-family: "Open Sans", sans-serif; font-weight: 400; color: var(--rust);
    letter-spacing: 1px; white-space: nowrap;
  }

  /* back */
  .back-brand { position: absolute; left: 0; right: 0; top: 150px; text-align: center; }
  .back-brand .wordmark { font-size: 40px; }
  .back-slogan { position: absolute; left: 0; right: 0; top: 235px; text-align: center; font-size: 17px; }
  .back-web {
    position: absolute; left: 0; right: 0; bottom: 70px; text-align: center;
    font-family: "Open Sans", sans-serif; color: var(--rust); font-size: 16px; letter-spacing: 4px;
  }

  /* front */
  .band-green { position: absolute; left: 0; right: 0; top: 170px; height: 150px; background: var(--green-deep); }
  .band-black { position: absolute; left: 0; right: 0; bottom: 0; height: 80px; background: var(--ink); border-top: 4px solid var(--paper); }

  .portrait {
    position: absolute; left: 60px; top: 60px; width: 175px; height: 160px;
    border: 4px solid #e9e9e9;
    background: linear-gradient(160deg, #d9d9d9, #7d7d7d 70%, #2a2a2e);
  }
  .person { position: absolute; left: 60px; top: 234px; }
  .person-name { font-family: "Playfair Display", serif; color: var(--paper); font-size: 22px; letter-spacing: 1px; line-height: 1.2; }
  .person-role, .person-nmls { font-family: "Playfair Display", serif; font-style: italic; color: var(--rust); font-size: 14px; line-height: 1.3; }

  .front-brand { position: absolute; right: 50px; top: 70px; text-align: right; }
  .front-brand .wordmark { font-size: 28px; }
  .front-slogan { position: absolute; right: 50px; top: 125px; font-size: 14px; }

  .contact { position: absolute; left: 345px; top: 182px; font-family: "Open Sans", sans-serif; color: var(--paper); font-size: 15px; }
  .contact-row { display: flex; align-items: center; gap: 10px; height: 23px; }
  .contact-row svg { width: 16px; height: 16px; flex: none; }
  .contact-row.plain { padding-left: 26px; }

  .apply { position: absolute; left: 60px; bottom: 14px; font-family: "Open Sans", sans-serif; color: var(--paper); font-size: 15px; line-height: 1.35; }
  .housing-badge { position: absolute; right: 60px; bottom: 18px; width: 40px; height: 40px; background: var(--paper); }
</style>
</head>
<body>
<main class="canvas">

  <section class="card card-back" aria-label="Card back">
    <div class="back-brand"><div class="wordmark">Keelbrook Mortgage</div></div>
    <div class="slogan back-slogan">your logical choice</div>
    <div class="back-web">www.keelbrook.com</div>
  </section>

  <section class="card card-front" aria-label="Card front">
    <div class="band-green"></div>
    <div class="band-black"></div>

    <div class="portrait" role="img" aria-label="Portrait photo of the loan officer"></div>

    <div class="person">
      <div class="person-name">DALE PRUITT</div>
      <div class="person-role">Job Title</div>
      <div class="person-nmls">NMLS# 572081</div>
    </div>

    <div class="front-brand"><div class="wordmark">Keelbrook Mortgage</div></div>
    <div class="slogan front-slogan">your logical choice</div>

    <div class="contact">
      <div class="contact-row">
        <svg viewBox="0 0 16 16"><path fill="#bc6225" d="M3 2h3l1 3-2 1a8 8 0 0 0 5 5l1-2 3 1v3a1 1 0 0 1-1 1A12 12 0 0 1 2 3a1 1 0 0 1 1-1z"/></svg>
        <span>000 000 0000</span>
      </div>
      <div class="contact-row">
        <svg viewBox="0 0 16 16"><rect x="4" y="1" width="8" height="14" rx="1.5" fill="none" stroke="#bc6225" stroke-width="1.6"/><circle cx="8" cy="12.5" r="1" fill="#bc6225"/></svg>
        <span>000 000 0000</span>
      </div>
      <div class="contact-row">
        <svg viewBox="0 0 16 16"><rect x="1" y="3" width="14" height="10" fill="#bc6225"/><path d="M1 3l7 6 7-6" fill="none" stroke="#1f7a62" stroke-width="1.2"/></svg>
        <span>youremail@example.com</span>
      </div>
      <div class="contact-row plain">2140 Cedar Ridge Ave Ste 300</div>
      <div class="contact-row plain">Austin, TX 78704</div>
    </div>

    <div class="apply">Apply online at:<br>www.keelbrook.com</div>
    <div class="housing-badge" role="img" aria-label="Equal housing lender badge"></div>
  </section>

</main>
</body>
</html>
```